QVR business card

Need a business card for a company that provides instructional design and elearning development services. The website is here: http://quorvane.studio/

I'm attaching a current logo, as well as the old business card design. While I like to keep it clean, the old design is too simplistic for my liking. The only idea I want to reuse from the old design is placing industry jargon on the back of the card, just need a better way to present it. But if you have other ideas for the back--feel free to experiment.

Please use the colors complementary to the color we have on the website. Thank you!

```html
<!DOCTYPE html>
<html lang="en">
<head>
<meta charset="utf-8">
<title>QVR Studio business card</title>
<link rel="stylesheet" href="https://fonts.googleapis.com/css2?family=Montserrat:wght@400;600;700&family=Oswald:wght@400;500&display=swap">
<style>
  :root {
    --teal: #13b2b1;
    --teal-deep: #0e9d9c;
    --gold: #d9cb92;
    --ink: #3b3b3b;
    --paper: #ffffff;
    --backdrop: #ece9e4;
  }
  * { box-sizing: border-box; margin: 0; padding: 0; }
  html, body { width: 1200px; height: 1120px; overflow: hidden; }
  body {
    background: var(--backdrop);
    font-family: "Montserrat", sans-serif;
    color: var(--ink);
    position: relative;
  }
  .card {
    position: absolute;
    left: 160px;
    width: 880px;
    height: 503px;
    overflow: hidden;
    box-shadow: 0 6px 18px rgba(0,0,0,0.18);
  }
  .card-front { top: 40px; background: var(--paper); }
  .card-back { top: 577px; background: var(--teal); }

  /* Front */
  .brand {
    position: absolute;
    left: 52px;
    top: 50px;
    display: flex;
    align-items: center;
    gap: 18px;
  }
  .brand-mark {
    width: 44px; height: 44px;
    background: var(--teal);
    border-radius: 50%;
  }
  .brand-name {
    font-weight: 700;
    font-size: 52px;
    letter-spacing: 1px;
    color: var(--teal);
  }
  .person { position: absolute; left: 60px; top: 248px; }
  .person-name {
    font-weight: 700;
    font-size: 25px;
    color: var(--teal);
  }
  .person-title {
    font-size: 24px;
    margin-top: 6px;
    color: var(--ink);
  }
  .front-bands { position: absolute; left: 0; bottom: 0; }
  .contact-list {
    position: absolute;
    left: 60px;
    top: 408px;
    list-style: none;
    font-size: 19px;
    color: var(--ink);
  }
  .contact-list li { display: flex; align-items: center; gap: 12px; height: 38px; }
  .contact-list svg { width: 18px; height: 18px; }
  .web-address {
    position: absolute;
    right: 40px;
    top: 448px;
    display: flex;
    align-items: center;
    gap: 12px;
    font-size: 21px;
    letter-spacing: 1.5px;
    color: var(--paper);
  }
  .web-address svg { width: 20px; height: 20px; }

  /* Back */
  .headline {
    position: absolute;
    left: 52px;
    top: 40px;
    font-family: "Oswald", sans-serif;
    font-weight: 500;
    font-size: 104px;
    line-height: 1.02;
    color: var(--paper);
  }
  .service-track { position: absolute; left: 300px; top: 34px; }
  .service-list {
    position: absolute;
    left: 392px;
    top: 38px;
    list-style: none;
    font-family: "Oswald", sans-serif;
    font-size: 34px;
    letter-spacing: 0.5px;
    color: var(--paper);
  }
  .service-list li { height: 70px; line-height: 60px; }
</style>
</head>
<body>

<section class="card card-front" aria-label="Card front">
  <div class="brand">
    <span class="brand-mark"></span>
    <span class="brand-name">QVR Studio</span>
  </div>

  <div class="person">
    <p class="person-name">Marek Holloway</p>
    <p class="person-title">Managing Director</p>
  </div>

  <svg class="front-bands" width="880" height="140" viewBox="0 0 880 140">
    <polygon points="0,0 520,0 590,140 0,140" fill="var(--gold)"/>
    <polygon points="560,60 880,60 880,140 590,140" fill="var(--teal)"/>
  </svg>

  <ul class="contact-list">
    <li>
      <svg viewBox="0 0 20 20"><path d="M5 2l3 4-2 2c1 2 3 4 5 5l2-2 4 3-2 3C9 17 3 11 2 5z" fill="var(--ink)"/></svg>
      555-013-2748
    </li>
    <li>
      <svg viewBox="0 0 20 20"><rect x="2" y="5" width="16" height="11" fill="var(--ink)"/><path d="M2 5l8 6 8-6" stroke="var(--gold)" stroke-width="1.5" fill="none"/></svg>
      mholloway@quorvane.studio
    </li>
  </ul>

  <p class="web-address">
    <svg viewBox="0 0 20 20" fill="none" stroke="var(--paper)" stroke-width="1.5"><circle cx="10" cy="10" r="8"/><ellipse cx="10" cy="10" rx="3.5" ry="8"/><path d="M2 10h16"/></svg>
    www.quorvane.studio
  </p>
</section>

<section class="card card-back" aria-label="Card back">
  <h2 class="headline">HOW<br>CAN<br>WE<br>HELP?</h2>

  <svg class="service-track" width="90" height="430" viewBox="0 0 90 430" fill="none" stroke="var(--paper)" stroke-width="2">
    <line x1="45" y1="40" x2="45" y2="394"/>
    <g class="service-node">
      <polygon points="45,18 84,36 45,54 6,36" fill="var(--teal)"/>
      <rect x="39" y="28" width="12" height="16" rx="2"/>
    </g>
    <g class="service-node" transform="translate(0,70)">
      <polygon points="45,18 84,36 45,54 6,36" fill="var(--teal)"/>
      <rect x="36" y="29" width="18" height="12"/>
    </g>
    <g class="service-node" transform="translate(0,140)">
      <polygon points="45,18 84,36 45,54 6,36" fill="var(--teal)"/>
      <path d="M38 27h14l-2 16-5 2-5-2z"/>
    </g>
    <g class="service-node" transform="translate(0,210)">
      <polygon points="45,18 84,36 45,54 6,36" fill="var(--teal)"/>
      <circle cx="45" cy="34" r="5"/><line x1="42" y1="42" x2="48" y2="42"/>
    </g>
    <g class="service-node" transform="translate(0,280)">
      <polygon points="45,18 84,36 45,54 6,36" fill="var(--teal)"/>
      <circle cx="45" cy="35" r="6"/><path d="M45 26v-2M54 35h2M34 35h2"/>
    </g>
    <g class="service-node" transform="translate(0,350)">
      <polygon points="45,18 84,36 45,54 6,36" fill="var(--teal)"/>
      <rect x="36" y="29" width="14" height="10"/><rect x="50" y="33" width="5" height="8"/>
    </g>
  </svg>

  <ul class="service-list">
    <li>MOBILE LEARNING SCORM</li>
    <li>INSTRUCTIONAL DESIGN LMS</li>
    <li>MOOCS ELEARNING HTML5</li>
    <li>ADULT LEARNING THEORY</li>
    <li>GAMIFICATION CLASSROOM</li>
    <li>XAPI BLENDED LEARNING</li>
  </ul>
</section>

</body>
</html>
```